Coastline Premier Retreats Business Card Design

Design a business card for Coastline Premier Retreats. Look at the website for colors and reference. Card should have logo, name, title, office number, mobile number, email, URL and a tagline like, "Luxury Hotel & Resort Email Marketing" (This might change).

https://www.coastlinepremierretreats.example

The rest I will leave up to your imagination.

Contact Information for Business Card

Logo, name, title, office number, mobile number, email, URL and a tagline like, "Luxury Hotel & Resort Email Marketing" (This might change).

```html
<!DOCTYPE html>
<html lang="en">
<head>
<meta charset="utf-8">
<title>Coastline Premier Retreats – Business Card</title>
<link rel="stylesheet" href="https://fonts.googleapis.com/css2?family=Open+Sans:wght@400;600;700;800&display=swap">
<style>
  :root {
    --stage: #232323;
    --card: #1f1f22;
    --card-shade: #19191c;
    --card-back: #1c1c1f;
    --emboss: #2c2c31;
    --orange: #f26f1c;
    --white: #f2f2f2;
  }
  * { box-sizing: border-box; margin: 0; padding: 0; }
  html, body { width: 1200px; height: 780px; overflow: hidden; }
  body {
    background: var(--stage);
    font-family: "Open Sans", Arial, sans-serif;
    position: relative;
  }
  .card {
    position: absolute;
    top: 235px;
    width: 540px;
    height: 310px;
    overflow: hidden;
  }
  .card--front { left: 40px; background: var(--card); }
  .card--back { left: 620px; background: var(--card-back); }

  .front__curve {
    position: absolute;
    left: 150px;
    top: 40px;
    width: 520px;
    height: 520px;
    border-radius: 50%;
    background: radial-gradient(circle at 35% 35%, #232327 0%, var(--card-shade) 70%);
    box-shadow: -8px -6px 22px rgba(0,0,0,.35);
  }
  .front__brand {
    position: absolute;
    left: 22px;
    top: 50%;
    width: 270px;
    transform: translate(-118px, -50%) rotate(-90deg);
    display: flex;
    align-items: center;
    justify-content: center;
    gap: 10px;
  }
  .front__brand-mark {
    width: 10px; height: 10px;
    background: var(--orange);
  }
  .front__brand-name {
    color: var(--white);
    font-weight: 700;
    font-size: 16px;
    letter-spacing: .5px;
    white-space: nowrap;
  }

  .front__details {
    position: absolute;
    right: 34px;
    top: 24px;
    text-align: right;
  }
  .person__name {
    font-size: 27px;
    font-weight: 700;
    line-height: 1.1;
  }
  .person__first { color: var(--orange); }
  .person__last { color: var(--white); }
  .person__title {
    color: var(--white);
    font-size: 13px;
    margin-top: 2px;
  }
  .front__accent {
    position: absolute;
    right: 0;
    top: 28px;
    width: 14px;
    height: 50px;
    background: var(--orange);
  }
  .tagline {
    color: var(--orange);
    font-size: 13px;
    line-height: 1.35;
    margin-top: 22px;
  }
  .contacts {
    list-style: none;
    margin-top: 20px;
  }
  .contacts li {
    display: flex;
    justify-content: flex-end;
    align-items: center;
    gap: 10px;
    color: var(--white);
    font-size: 12.5px;
    line-height: 21px;
  }
  .contacts svg { width: 13px; height: 13px; flex: none; }

  .back__brand {
    position: absolute;
    inset: 0;
    display: flex;
    align-items: center;
    justify-content: center;
    color: var(--emboss);
    font-weight: 800;
    font-size: 30px;
    letter-spacing: 1px;
  }
</style>
</head>
<body>

<section class="card card--front" aria-label="Business card front">
  <div class="front__curve"></div>

  <div class="front__brand">
    <span class="front__brand-mark"></span>
    <span class="front__brand-name">Coastline Premier Retreats</span>
  </div>

  <div class="front__accent"></div>

  <div class="front__details">
    <h1 class="person__name"><span class="person__first">Marina</span> <span class="person__last">Kovalen</span></h1>
    <p class="person__title">Managing Director</p>

    <p class="tagline">Luxury Hotel &amp;<br>Resort Email Marketing</p>

    <ul class="contacts">
      <li>(555) 214-0386
        <svg viewBox="0 0 16 16" aria-hidden="true"><path fill="#f26f1c" d="M3.6 1.2l2.3 2.6-1.3 1.8c.9 2 2.3 3.5 4.2 4.4l1.8-1.3 2.6 2.3-1.2 2.2C6.8 13.6 2.5 9.3 1.4 3.4z"/></svg>
      </li>
      <li>(555) 310-4477
        <svg viewBox="0 0 16 16" aria-hidden="true"><rect x="4" y="1" width="8" height="14" rx="1.5" fill="none" stroke="#f26f1c" stroke-width="1.6"/><circle cx="8" cy="12.5" r=".9" fill="#f26f1c"/></svg>
      </li>
      <li>www.coastlinepremierretreats.example
        <svg viewBox="0 0 16 16" aria-hidden="true"><circle cx="8" cy="8" r="6.5" fill="none" stroke="#f26f1c" stroke-width="1.5"/><ellipse cx="8" cy="8" rx="2.8" ry="6.5" fill="none" stroke="#f26f1c" stroke-width="1.2"/><path d="M1.5 8h13" stroke="#f26f1c" stroke-width="1.2"/></svg>
      </li>
      <li>info@coastlinepremierretreats.example
        <svg viewBox="0 0 16 16" aria-hidden="true"><rect x="1" y="3" width="14" height="10" rx="1" fill="#f26f1c"/><path d="M1.5 3.8L8 9l6.5-5.2" fill="none" stroke="#1f1f22" stroke-width="1.3"/></svg>
      </li>
    </ul>
  </div>
</section>

<section class="card card--back" aria-label="Business card back">
  <p class="back__brand">Coastline Premier Retreats</p>
</section>

</body>
</html>
```